RevelHubQZ Business Cards

Front
Has logo with a design. Website address (www.revelhubqz-example.net)
Has slogan (discover the nightlife)
Has phone number (5182297734)
Should be bold and stands out.

Back
Has details about what we offer.

Events
Search upcoming events
Submit events
Party Image Gallery
View and download HQ party images
Sign up as a contributing event photographer and get paid!
Tickets
Sell your event tickets online for free!
Direct pay
No ticket fee

Target Market(s)

These cards will be handed out in clubs and events to patrons.

Industry/Entity Type

Business

Contact Information for Business Card

Should match or mirror our website in some sort of way. Visit the website to get ideas.

Requirements
Must have
• Must be designed for a 3x3 inch card.

```html
<!DOCTYPE html>
<html lang="en">
<head>
<meta charset="utf-8">
<title>RevelHubQZ Business Cards</title>
<link rel="stylesheet" href="https://fonts.googleapis.com/css2?family=Roboto:wght@400;700&display=swap">
<style>
  :root {
    --stage: #3a3a3a;
    --card-dark: #000000;
    --card-light: #fbfbfb;
    --brand-blue: #2e9fd6;
    --brand-pink: #e0348f;
    --text-grey: #555555;
    --white: #ffffff;
  }
  * { margin: 0; padding: 0; box-sizing: border-box; }
  html, body {
    width: 1200px;
    height: 750px;
    overflow: hidden;
    background: var(--stage);
    font-family: "Roboto", Arial, sans-serif;
  }
  .canvas {
    position: relative;
    width: 1200px;
    height: 750px;
  }
  .card {
    position: absolute;
    top: 233px;
    width: 285px;
    height: 285px;
  }
  .card--front { left: 298px; background: var(--card-dark); }
  .card--back  { left: 617px; background: var(--card-light); }

  .brand {
    position: absolute;
    left: 0;
    right: 0;
    display: flex;
    flex-direction: column;
    align-items: center;
  }
  .card--front .brand { top: 48px; }
  .card--back .brand  { top: 53px; }
  .brand__row {
    display: flex;
    align-items: center;
    gap: 8px;
  }
  .brand__dot {
    width: 26px;
    height: 26px;
    border-radius: 50%;
    background: var(--brand-blue);
  }
  .brand__name {
    font-size: 24px;
    font-weight: 400;
    color: var(--brand-blue);
    letter-spacing: -0.3px;
  }
  .brand__slogan {
    margin-top: 2px;
    padding-left: 34px;
    font-size: 8px;
    letter-spacing: 3.2px;
    color: var(--white);
  }
  .card--back .brand__slogan { color: var(--text-grey); }

  .phone-band {
    position: absolute;
    top: 133px;
    left: 0;
    width: 100%;
    height: 51px;
    background: var(--brand-blue);
    border-top: 2px solid var(--brand-pink);
    border-bottom: 2px solid var(--brand-pink);
    display: flex;
    align-items: center;
    justify-content: center;
  }
  .phone-band__number {
    font-size: 37px;
    font-weight: 700;
    color: var(--white);
    letter-spacing: 0.5px;
  }
  .website {
    position: absolute;
    top: 228px;
    left: 0;
    width: 100%;
    text-align: center;
    font-size: 16px;
    color: var(--brand-pink);
  }

  .offer {
    position: absolute;
    top: 180px;
    left: 0;
    width: 100%;
    text-align: center;
  }
  .offer__title {
    font-size: 12px;
    font-weight: 400;
    color: var(--brand-blue);
    margin-bottom: 5px;
  }
  .offer__list { list-style: none; }
  .offer__line {
    font-size: 8.3px;
    line-height: 11.2px;
    color: var(--text-grey);
  }
  .offer__sep {
    display: inline-block;
    width: 4px;
    height: 4px;
    margin: 0 3px 1px;
    border-radius: 50%;
    background: var(--brand-blue);
  }
</style>
</head>
<body>
<main class="canvas">
  <section class="card card--front" aria-label="Card front">
    <div class="brand">
      <div class="brand__row">
        <span class="brand__dot"></span>
        <span class="brand__name">RevelHubQZ</span>
      </div>
      <span class="brand__slogan">discover the nightlife</span>
    </div>
    <div class="phone-band">
      <span class="phone-band__number">5182297734</span>
    </div>
    <p class="website">www.revelhubqz-example.net</p>
  </section>

  <section class="card card--back" aria-label="Card back">
    <div class="brand">
      <div class="brand__row">
        <span class="brand__dot"></span>
        <span class="brand__name">RevelHubQZ</span>
      </div>
      <span class="brand__slogan">discover the nightlife</span>
    </div>
    <div class="offer">
      <h2 class="offer__title">Events</h2>
      <ul class="offer__list">
        <li class="offer__line">Search upcoming events<span class="offer__sep"></span>Submit events</li>
        <li class="offer__line">Party Image Gallery<span class="offer__sep"></span>View &amp; download HQ party images</li>
        <li class="offer__line">Sign up as a contributing event photographer &amp; get paid!</li>
        <li class="offer__line">Tickets<span class="offer__sep"></span>Sell your event tickets online for free!</li>
        <li class="offer__line">Direct pay<span class="offer__sep"></span>No ticket fee</li>
      </ul>
    </div>
  </section>
</main>
</body>
</html>
```